Brave Lotus - Fitness Retreat

Tri Fold Brochure & Double sided A4 version options, see attached mockup.

Target Market: Women 18-50, Asian mainly .

Kelvar Fitness Presents - Brave Lotus Fitness Retreats:

Something communicating the spirit of getting fit, being strong, eating healthy and strong sense of the feminine.

Industry/Entity Type

Fitness

```html
<!DOCTYPE html>
<html lang="en">
<head>
<meta charset="utf-8">
<title>Brave Lotus Fitness Retreats – Tri-fold Brochure</title>
<link rel="stylesheet" href="https://fonts.googleapis.com/css2?family=Lilita+One&family=Open+Sans:wght@400;700;800&family=PT+Serif:ital,wght@0,400;0,700;1,700&display=swap">
<style>
:root{
  --red:#c1272d;
  --red-dark:#8f1c21;
  --cream:#f4ece6;
  --ink:#3b2b26;
  --pink-text:#f7d9d6;
  --hint-text:#f6b27a;
  --page:#e6e6e6;
  --white:#ffffff;
}
*{box-sizing:border-box;margin:0;padding:0}
html,body{width:1200px;height:937px;overflow:hidden}
body{background:var(--page);font-family:"PT Serif",Georgia,serif;color:var(--ink);position:relative}
.spread{position:absolute;left:280px;width:640px;height:450px;display:flex;box-shadow:0 4px 14px rgba(0,0,0,.18);background:var(--cream)}
.spread-outer{top:12px}
.spread-inner{top:475px}
.panel{position:relative;width:213.33px;height:450px;overflow:hidden;background:var(--cream)}
.panel + .panel{border-left:1px solid rgba(0,0,0,.06)}
.photo{position:absolute;left:0;width:100%}
.wave{position:absolute;left:0;width:100%;display:block}
.red-block{position:absolute;left:0;top:0;width:100%;background:var(--red)}
.heading{font-family:"Open Sans",Arial,sans-serif;font-weight:800;text-transform:uppercase;font-size:8px;letter-spacing:.2px}
.list{list-style:none;font-family:"Open Sans",Arial,sans-serif;font-size:5.6px;line-height:8.2px;color:var(--white)}
.list li{padding-left:8px;position:relative}
.list li::before{content:"";position:absolute;left:1px;top:2.6px;width:3px;height:3px;border-radius:50%;background:var(--white)}
.brand-lockup{position:absolute;left:0;width:100%;text-align:center}
.brand-name{font-family:"Lilita One",Impact,sans-serif;color:var(--red);font-size:22px;letter-spacing:.5px;line-height:1}
.brand-sub{font-family:"Open Sans",Arial,sans-serif;font-weight:700;font-size:7px;letter-spacing:1.2px;color:var(--ink)}
.mark{display:inline-flex;align-items:center;gap:4px;font-family:"Open Sans",Arial,sans-serif;font-weight:800;font-size:8px;color:var(--red)}
.mark::before{content:"";width:9px;height:9px;background:var(--red)}
/* outer */
.inclusions{position:absolute;left:14px;top:16px;right:10px;color:var(--white)}
.inclusions .heading{margin-bottom:3px}
.exclusions{margin-top:8px}
.tagline{position:absolute;left:10px;right:10px;top:236px;text-align:center;font-style:italic;font-weight:700;font-size:9.5px;line-height:12px;color:var(--ink)}
.partner-box{position:absolute;left:18px;right:18px;top:305px;height:38px;background:var(--white);display:flex;align-items:center;justify-content:space-around}
.contacts{position:absolute;left:0;right:0;top:370px;text-align:center;color:var(--white);font-size:6.2px;line-height:8.4px}
.contacts p + p{margin-top:0}
.contacts .group + .group{margin-top:6px}
.terms{position:absolute;left:14px;top:16px;right:10px;color:var(--white)}
.terms .heading{margin-bottom:3px}
.price-badge{position:absolute;left:14px;top:172px;width:52px;height:52px;border-radius:50%;background:var(--red);border:2px dashed var(--white);box-shadow:0 0 0 2px var(--red);color:var(--white);text-align:center;font-family:"Lilita One",Impact,sans-serif;font-size:15px;line-height:1;padding-top:13px}
.price-badge small{display:block;font-size:7px}
.cover-motto{position:absolute;left:76px;top:176px;font-family:"PT Serif",Georgia,serif;font-weight:700;font-size:10px;line-height:12px;color:var(--ink)}
/* inner */
.activities-title{position:absolute;left:0;right:0;top:10px;text-align:center;font-family:"Lilita One",Impact,sans-serif;font-style:italic;color:var(--red);font-size:12px;letter-spacing:.5px}
.schedule{position:absolute;left:8px;right:8px;top:28px;border-collapse:separate;border-spacing:0 2px;font-family:"Open Sans",Arial,sans-serif;width:197px}
.schedule th{background:var(--red);color:var(--white);font-size:6px;font-weight:800;letter-spacing:.8px;padding:2px 0;text-transform:uppercase}
.schedule th:first-child{width:30px}
.schedule td{background:var(--white);font-size:4.9px;line-height:6.1px;padding:2px 3px;vertical-align:middle}
.schedule td.day{font-weight:800;font-size:6.2px;text-align:center;color:var(--ink);background:var(--cream)}
.schedule b{font-weight:700;color:var(--red)}
.info{position:absolute;left:12px;right:10px;font-size:5.4px;line-height:6.6px}
.info h3{font-family:"Open Sans",Arial,sans-serif;font-weight:800;font-size:6.8px;text-transform:uppercase;margin-top:5px;margin-bottom:1px}
.info h3:first-child{margin-top:0}
.info-on-red h3{color:var(--white)}
.info-on-red p{color:var(--pink-text)}
.info-on-cream h3{color:var(--red)}
.info-on-cream p{color:var(--ink)}
.hints-title{position:absolute;left:0;right:0;top:10px;text-align:center;font-family:"Open Sans",Arial,sans-serif;font-weight:800;font-size:8px;color:var(--ink);letter-spacing:.5px}
.hints p{color:var(--hint-text)}
</style>
</head>
<body>

<!-- Outside of brochure -->
<section class="spread spread-outer">

  <!-- Inside flap -->
  <div class="panel panel-flap">
    <div class="photo" style="top:0;height:285px;background:linear-gradient(160deg,#6d8f4a,#a7b86a 45%,#c99776 70%,#4c5a33)" role="img" aria-label="Photo of a fit woman in sportswear posing outdoors among tropical plants"></div>
    <svg class="wave" style="top:262px;height:34px" viewBox="0 0 214 34" preserveAspectRatio="none"><path d="M0 14C70 36 140 0 214 10V34H0Z" fill="var(--cream)"/><path d="M0 14C70 36 140 0 214 10V16C140 8 70 40 0 22Z" fill="var(--red)"/></svg>
    <div class="brand-lockup" style="top:305px">
      <span class="mark">Kelvar Fitness</span>
      <div class="brand-name" style="margin-top:8px">BRAVE LOTUS</div>
      <div class="brand-sub">BOOT CAMP BALI RETREATS</div>
    </div>
    <div class="photo" style="top:385px;height:65px;background:linear-gradient(120deg,#3f6b3a,#8aa765 60%,#d7c7a3)" role="img" aria-label="Photo of women exercising together in a tropical garden"></div>
    <svg class="wave" style="top:375px;height:26px" viewBox="0 0 214 26" preserveAspectRatio="none"><path d="M0 0H214V10C140 28 70 2 0 18Z" fill="var(--cream)"/><path d="M0 18C70 2 140 28 214 10V16C140 32 70 8 0 24Z" fill="var(--red)"/></svg>
  </div>

  <!-- Back panel -->
  <div class="panel panel-back">
    <div class="red-block" style="height:215px"></div>
    <svg class="wave" style="top:205px;height:28px" viewBox="0 0 214 28" preserveAspectRatio="none"><path d="M0 0H214V8C140 30 70 2 0 22Z" fill="var(--red)"/></svg>
    <div class="inclusions">
      <h2 class="heading">Inclusions</h2>
      <ul class="list">
        <li>Six nights shared villa accommodation</li>
        <li>Airport transfers on arrival and departure</li>
        <li>Three healthy Balinese meals daily</li>
        <li>All fitness sessions and workshops</li>
        <li>Daily yoga and stretching</li>
        <li>Volcano sunrise trek and hot springs</li>
        <li>Retreat T-shirt and water bottle</li>
      </ul>
      <div class="exclusions">
        <h2 class="heading">Exclusions</h2>
        <ul class="list">
          <li>Flights to and from Bali</li>
          <li>Travel insurance</li>
          <li>Alcohol and soft drinks</li>
          <li>Extra tours, massages and personal shopping</li>
        </ul>
      </div>
    </div>
    <p class="tagline">Be prepared to challenge yourself<br>and have a lot of fun.<br>Most importantly pack an open mind!<br>You are about to have a<br>very unique experience.</p>
    <div class="partner-box">
      <span class="mark">Kelvar Fitness</span>
      <span class="mark">Open Island</span>
    </div>
    <svg class="wave" style="top:345px;height:105px" viewBox="0 0 214 105" preserveAspectRatio="none"><path d="M0 14C70 -4 140 26 214 6V105H0Z" fill="var(--red)"/></svg>
    <div class="contacts">
      <div class="group">
        <p>hello@kelvarfitness.com</p>
        <p>+62 811 000 4821</p>
        <p>www.kelvarfitness.com</p>
      </div>
      <div class="group">
        <p>info@openisland.com</p>
        <p>+62 811 000 7315</p>
        <p>www.openisland.com</p>
      </div>
    </div>
  </div>

  <!-- Front cover -->
  <div class="panel panel-cover">
    <div class="red-block" style="height:150px"></div>
    <svg class="wave" style="top:140px;height:28px" viewBox="0 0 214 28" preserveAspectRatio="none"><path d="M0 0H214V20C140 0 70 30 0 10Z" fill="var(--red)"/></svg>
    <div class="terms">
      <h2 class="heading">Terms &amp; Conditions</h2>
      <ul class="list">
        <li>Deposit of 30% secures your place</li>
        <li>Balance due six weeks before arrival</li>
        <li>Deposits are non refundable</li>
        <li>Travel insurance is compulsory</li>
        <li>Guests must disclose medical conditions</li>
        <li>Program may change due to weather</li>
      </ul>
    </div>
    <div class="price-badge">1650<small>pp</small></div>
    <p class="cover-motto">Fitness, Fun,<br>Friendship<br>&amp; Adventure</p>
    <svg class="wave" style="top:250px;height:22px" viewBox="0 0 214 22" preserveAspectRatio="none"><path d="M0 16C70 0 140 22 214 6V12C140 28 70 6 0 22Z" fill="var(--red)"/></svg>
    <div class="brand-lockup" style="top:276px">
      <div class="brand-name">BRAVE LOTUS</div>
      <div class="brand-sub">BOOT CAMP BALI RETREATS</div>
    </div>
    <div class="photo" style="top:330px;height:120px;background:linear-gradient(140deg,#5d8a45,#a8bf7a 50%,#c98f86 75%,#6b8f52)" role="img" aria-label="Photo of women boxing with pink gloves on a green lawn"></div>
    <svg class="wave" style="top:322px;height:24px" viewBox="0 0 214 24" preserveAspectRatio="none"><path d="M0 0H214V14C140 -2 70 26 0 10Z" fill="var(--cream)"/><path d="M0 10C70 26 140 -2 214 14V18C140 4 70 32 0 16Z" fill="var(--red)"/></svg>
  </div>
</section>

<!-- Inside of brochure -->
<section class="spread spread-inner">

  <!-- Activities -->
  <div class="panel panel-activities">
    <h2 class="activities-title">BRAVE LOTUS ACTIVITIES</h2>
    <table class="schedule">
      <thead><tr><th>Days</th><th>Activities</th></tr></thead>
      <tbody>
        <tr><td class="day">ONE</td><td><b>2pm:</b> Group Transfer from Airport or nearby Hotel.<br><b>5pm:</b> Settle into your Bungalow with a welcome Lemongrass tea.<br><b>6pm:</b> Time to get to know each other and Introduction to the program.<br><b>7pm:</b> Dinner Balinese Style</td></tr>
        <tr><td class="day">TWO</td><td><b>6am:</b> Stretching – Assessment – All Fitness Intro<br><b>8am:</b> Breakfast<br><b>9am:</b> Fun Jungle Trek Fitness adventure<br><b>12n:</b> Lunch<br><b>2pm:</b> Body Weight Management Work Shop<br><b>4pm:</b> Muay Thai Strength &amp; Conditioning<br><b>7pm:</b> Dinner</td></tr>
        <tr><td class="day">THREE</td><td><b>3am:</b> Departure for Meeting Sunrise Volcano Climb<br><b>9am:</b> Rests at the Lakeside Hot Springs<br><b>12n:</b> Lunch<br><b>3pm:</b> Home Training Work Shop<br><b>6.30:</b> Pilates<br><b>7pm:</b> Dinner</td></tr>
        <tr><td class="day">FOUR</td><td><b>7am:</b> Breakfast<br><b>8.30:</b> Interval Training on hills<br><b>12n:</b> Lunch<br><b>2pm:</b> Nutrition &amp; Diet Work Shop<br><b>4pm:</b> Yoga<br><b>7pm:</b> Dinner</td></tr>
        <tr><td class="day">FIVE</td><td><b>6am:</b> All Fitness – HIIT Strength &amp; Conditioning<br><b>8am:</b> Breakfast<br><b>9am:</b> Jungle Trek<br><b>12n:</b> Lunch<br><b>2pm:</b> Traditional Balinese Dance Class<br><b>7pm:</b> Dinner</td></tr>
        <tr><td class="day">SIX</td><td><b>6am:</b> Final Training – 5 Fitness Elements – Final Challenge – Fitness Performance &amp; Review<br><b>8am:</b> Breakfast<br><b>9am:</b> Sister Talk / Motivational Speaking<br><b>12n:</b> Farewell – Departure to Airport or next destination</td></tr>
      </tbody>
    </table>
    <svg class="wave" style="top:372px;height:26px" viewBox="0 0 214 26" preserveAspectRatio="none"><path d="M0 20C70 0 140 26 214 8V26H0Z" fill="var(--red)"/></svg>
    <div class="photo" style="top:392px;height:58px;background:linear-gradient(120deg,#9cb07a,#d9a0a8 45%,#c3c9b0 80%)" role="img" aria-label="Photo of women in boxing gloves during a training session"></div>
  </div>

  <!-- Packing notes -->
  <div class="panel panel-notes">
    <div class="red-block" style="height:215px"></div>
    <svg class="wave" style="top:205px;height:26px" viewBox="0 0 214 26" preserveAspectRatio="none"><path d="M0 0H214V20C140 0 70 28 0 8Z" fill="var(--red)"/></svg>
    <div class="info info-on-red" style="top:12px">
      <h3>Training Sessions</h3>
      <p>Bring comfortable workout gear and a sports water bottle. Two pairs of shoes are ideal.</p>
      <h3>Yoga &amp; Stretch Sessions</h3>
      <p>Comfortable stretch pants and tees.</p>
      <h3>Walks &amp; Treks</h3>
      <p>Closed shoes with good grip for jungle and rice field trails.</p>
      <h3>Shoes</h3>
      <p>Bring sandals for outdoors and sturdy trainers for training.</p>
      <h3>Everyday</h3>
      <p>Pack light cotton clothes, a hat, sunscreen, insect repellent and a raincoat for sudden tropical showers. Evenings can be cool.</p>
      <h3>Banned Narcotics</h3>
      <p>Do not even think about bringing them. You will be removed from the property.</p>
    </div>
    <div class="info info-on-cream" style="top:236px">
      <h3>Bits &amp; Pieces</h3>
      <p>Bring an adapter suitable for Indonesia, a small torch, a reusable shopping bag and a good book for quiet afternoons.</p>
      <h3>Volcano / Hot Springs</h3>
      <p>It's cold before sunrise. Wear layers, a light jacket, gloves and trainers with good grip.</p>
      <h3>Group Transfers</h3>
      <p>Your package includes group transfers to the retreat from the airport at 2pm on Day 1 and back on the last day.</p>
      <h3>Safety</h3>
      <p>Travel insurance is compulsory. Bring a photocopy of your passport and any medication you need.</p>
    </div>
    <svg class="wave" style="top:372px;height:26px" viewBox="0 0 214 26" preserveAspectRatio="none"><path d="M0 8C70 26 140 0 214 20V26H0Z" fill="var(--red)"/></svg>
    <div class="photo" style="top:392px;height:58px;background:linear-gradient(120deg,#6f8f50,#b8c48c 50%,#7d8a5e)" role="img" aria-label="Photo of women training with a large tyre in a rice field"></div>
  </div>

  <!-- Travel hints -->
  <div class="panel panel-hints">
    <div class="red-block" style="height:225px"></div>
    <svg class="wave" style="top:215px;height:26px" viewBox="0 0 214 26" preserveAspectRatio="none"><path d="M0 0H214V10C140 28 70 2 0 20Z" fill="var(--red)"/></svg>
    <h2 class="hints-title">HANDY TRAVEL HINTS</h2>
    <div class="info info-on-red hints" style="top:26px">
      <h3>Air Port (International)</h3>
      <p>Check your passport is valid for six months. Visa on arrival is paid at the airport in cash. Look for our driver holding your name after customs.</p>
      <h3>Staying in Touch</h3>
      <p>Wifi is available in common areas. Local SIM cards are cheap and easy to buy at the airport or in town. Let family know your plans before you fly.</p>
      <h3>Drinking Water</h3>
      <p>Only drink bottled water, including when brushing teeth.</p>
    </div>
    <div class="info info-on-cream" style="top:250px">
      <h3>Money</h3>
      <p>Local currency is Rupiah. ATMs and exchange counters are at the airport. Bring some cash for tips and extras.</p>
      <h3>Meals</h3>
      <p>Meals are fresh, healthy and local. We eat together and share our style of clean Balinese cooking. Tell us about any allergies.</p>
      <h3>Alcohol</h3>
      <p>The only alcohol we serve is local beer. Bring your own wine if you wish.</p>
    </div>
    <svg class="wave" style="top:368px;height:26px" viewBox="0 0 214 26" preserveAspectRatio="none"><path d="M0 20C70 0 140 26 214 8V26H0Z" fill="var(--red)"/></svg>
    <div class="photo" style="top:388px;height:62px;background:linear-gradient(180deg,#b9c4c8,#8a8f8c 55%,#4a4540)" role="img" aria-label="Photo of women doing a group workout on a black sand beach"></div>
  </div>
</section>

</body>
</html>
```